Business Card Design Project

Keep it simple , using logo and colors that compliment. Logo on one side with complimentary back ground color. Other side, personal info with possible complimentary design/colors

Target Market(s)

we are a non for profit that will be seeking donations . Both monetary and in kind

Industry/Entity Type

Business

Font styles to use
Sans Serif

Colors

Designer to choose colors to be used in the design.

```html
<!DOCTYPE html>
<html lang="en">
<head>
<meta charset="utf-8">
<title>Open Hands Trust – Business Card</title>
<link rel="stylesheet" href="https://fonts.googleapis.com/css2?family=Lato:wght@300;400;700;900&display=swap">
<style>
  :root {
    --navy: #1e2647;
    --yellow: #e6d400;
    --paper: #f7f7f7;
    --ink: #1e2647;
    --text-grey: #3a3a3a;
    --backdrop: #3a3a3a;
  }
  * { box-sizing: border-box; margin: 0; padding: 0; }
  html, body { width: 1200px; height: 997px; overflow: hidden; }
  body {
    background: var(--backdrop);
    font-family: "Lato", sans-serif;
    position: relative;
  }
  .card {
    position: absolute;
    left: 280px;
    width: 640px;
    height: 366px;
    border-radius: 22px;
    overflow: hidden;
  }
  .card--back { top: 90px; background: var(--navy); }
  .card--front { top: 520px; background: var(--paper); }

  .brand {
    position: absolute;
    display: flex;
    align-items: center;
    gap: 14px;
  }
  .brand__dot {
    flex: none;
    border-radius: 50%;
    background: var(--yellow);
  }
  .brand__name {
    font-family: "Lato", sans-serif;
    font-weight: 300;
    line-height: 1.1;
    white-space: nowrap;
  }
  .card--back .brand {
    left: 0; right: 0; top: 0; bottom: 0;
    justify-content: center;
  }
  .card--back .brand__dot { width: 22px; height: 22px; }
  .card--back .brand__name { color: var(--yellow); font-size: 44px; }

  .card--front .brand {
    left: 36px; top: 100px; width: 240px;
  }
  .card--front .brand__dot { width: 16px; height: 16px; }
  .card--front .brand__name { color: var(--navy); font-size: 34px; font-weight: 700; }

  .contact {
    position: absolute;
    left: 300px;
    top: 44px;
  }
  .contact__name {
    font-weight: 900;
    font-size: 22px;
    color: var(--ink);
    letter-spacing: 0.5px;
  }
  .contact__role {
    font-weight: 700;
    font-size: 12px;
    color: var(--text-grey);
    letter-spacing: 1px;
    margin-bottom: 16px;
  }
  .contact__list { list-style: none; }
  .contact__item {
    display: flex;
    align-items: flex-start;
    gap: 10px;
    font-size: 15px;
    color: var(--text-grey);
    line-height: 18px;
    margin-bottom: 10px;
  }
  .contact__icon { flex: none; width: 20px; height: 20px; }

  .band-rule {
    position: absolute;
    left: 0; right: 0;
    top: 284px; height: 7px;
    background: var(--yellow);
  }
  .band {
    position: absolute;
    left: 0; right: 0;
    top: 291px; bottom: 0;
    background: var(--navy);
  }
</style>
</head>
<body>

<section class="card card--back" aria-label="Card back">
  <div class="brand">
    <span class="brand__dot"></span>
    <span class="brand__name">Open Hands Trust</span>
  </div>
</section>

<section class="card card--front" aria-label="Card front">
  <div class="brand">
    <span class="brand__dot"></span>
    <span class="brand__name">Open Hands<br>Trust</span>
  </div>

  <div class="contact">
    <div class="contact__name">YOUR NAME</div>
    <div class="contact__role">OWNER &amp; DIRECTOR</div>
    <ul class="contact__list">
      <li class="contact__item">
        <svg class="contact__icon" viewBox="0 0 20 20"><circle cx="10" cy="10" r="10" fill="var(--navy)"/><path d="M6.5 5.5l2 0 1 2.5-1.3 1a6 6 0 0 0 2.8 2.8l1-1.3 2.5 1v2c0 .6-.5 1-1 1A8.5 8.5 0 0 1 5.5 6.5c0-.5.4-1 1-1z" fill="#fff"/></svg>
        0049 170 5558210
      </li>
      <li class="contact__item">
        <svg class="contact__icon" viewBox="0 0 20 20"><circle cx="10" cy="10" r="10" fill="var(--navy)"/><rect x="7" y="4.5" width="6" height="3" fill="#fff"/><rect x="4.5" y="8" width="11" height="5" rx="1" fill="#fff"/><rect x="7" y="12" width="6" height="3.5" fill="#fff" stroke="var(--navy)" stroke-width=".8"/></svg>
        0049 170 5558211
      </li>
      <li class="contact__item">
        <svg class="contact__icon" viewBox="0 0 20 20"><circle cx="10" cy="10" r="10" fill="var(--navy)"/><rect x="4.5" y="6" width="11" height="8" fill="#fff"/><path d="M4.5 6l5.5 4.5L15.5 6" fill="none" stroke="var(--navy)" stroke-width="1"/></svg>
        info@openhandstrust.org
      </li>
      <li class="contact__item">
        <svg class="contact__icon" viewBox="0 0 20 20"><circle cx="10" cy="10" r="10" fill="var(--navy)"/><g fill="none" stroke="#fff" stroke-width="1.6"><rect x="5" y="8.5" width="6" height="3.5" rx="1.75" transform="rotate(-45 8 10.25)"/><rect x="9" y="8" width="6" height="3.5" rx="1.75" transform="rotate(-45 12 9.75)"/></g></svg>
        www.openhandstrust.org
      </li>
      <li class="contact__item">
        <svg class="contact__icon" viewBox="0 0 20 20"><circle cx="10" cy="10" r="10" fill="var(--navy)"/><path d="M10 4a4 4 0 0 0-4 4c0 3 4 7.5 4 7.5s4-4.5 4-7.5a4 4 0 0 0-4-4z" fill="#fff"/><circle cx="10" cy="8" r="1.5" fill="var(--navy)"/></svg>
        Lindenweg 12<br>60311 Musterstadt
      </li>
    </ul>
  </div>

  <div class="band-rule"></div>
  <div class="band"></div>
</section>

</body>
</html>
```